Pebble Hop - mobile play centre poster designs

Who are we - we are a mobile playground business that specialises in providing entertainment to children in a safe, clean environment either at home or in a function centre. Brief - create 4 different signs to be displayed on our playgrounds. Please find attached 3 photos from our competitors to use as a guide. Corflute sign - size A1 Toddler zone - size A1 Playground rules - size A4 No climbing - size 20cmx8cm sending through photos and documents now.
Colors
Designer to choose colors to be used in the design.
Requirements
Must have
- Colour, be very specific with the rules, pictures

```html
<!DOCTYPE html>
<html lang="en">
<head>
<meta charset="utf-8">
<title>Pebble Hop – Play Centre Signs</title>
<link rel="stylesheet" href="https://fonts.googleapis.com/css2?family=Roboto:wght@400;500;700;900&display=swap">
<style>
  :root {
    --red: #e8212a;
    --orange: #f58220;
    --yellow: #fcc417;
    --green: #8dc63f;
    --blue: #0f75bc;
    --purple: #7d3c8f;
    --ink: #111111;
    --grey: #6d6e71;
    --paper: #ffffff;
  }
  * { box-sizing: border-box; margin: 0; padding: 0; }
  html, body { width: 1200px; height: 970px; overflow: hidden; background: var(--paper); }
  body { position: relative; font-family: "Roboto", Arial, sans-serif; color: var(--ink); }

  .sign { position: absolute; }
  .sign__frame {
    position: absolute; inset: 0;
    background: linear-gradient(135deg, var(--purple), var(--blue) 22%, var(--green) 42%, var(--yellow) 60%, var(--orange) 78%, var(--red));
  }
  .sign__panel {
    position: absolute;
    background: var(--paper);
    box-shadow: 0 0 3px rgba(0,0,0,.25);
  }
  .abs { position: absolute; }
  .center { left: 0; right: 0; text-align: center; }

  .brand { display: flex; flex-direction: column; align-items: center; }
  .brand__name { display: flex; align-items: center; gap: 8px; font-weight: 900; color: var(--red); font-size: 34px; line-height: 1; }
  .brand__dot { width: 20px; height: 20px; border-radius: 50%; background: var(--green); }
  .brand__tag { font-weight: 500; color: var(--grey); font-size: 14px; letter-spacing: 1px; margin-top: 4px; }

  .accent { color: var(--red); }
  .icon { display: block; fill: none; stroke: var(--ink); stroke-width: 2; stroke-linecap: round; stroke-linejoin: round; }

  /* Sign 1 */
  .sign--age { left: 97px; top: 94px; width: 523px; height: 370px; }
  .sign--age .sign__panel { left: 29px; top: 24px; width: 466px; height: 322px; }
  .age-title { font-size: 39px; font-weight: 700; color: var(--red); top: 128px; line-height: 1; }
  .age-note { left: 30px; display: flex; align-items: center; font-size: 17px; font-weight: 500; }
  .age-note .icon { width: 36px; height: 36px; margin-right: 32px; }

  /* Sign 2 */
  .sign--toddler { left: 97px; top: 522px; width: 523px; height: 369px; }
  .sign--toddler .sign__panel { left: 29px; top: 24px; width: 466px; height: 320px; }
  .toddler-text { top: 110px; font-size: 15.5px; font-weight: 500; line-height: 24.6px; white-space: nowrap; }
  .toddler-text .big { font-size: 18px; }

  /* Sign 3 */
  .sign--rules { left: 709px; top: 94px; width: 401px; height: 568px; }
  .sign--rules .sign__panel { left: 19px; top: 20px; width: 362px; height: 526px; }
  .rules-intro { top: 106px; font-size: 12.5px; font-weight: 500; line-height: 20px; }
  .rules-title { top: 152px; font-size: 29px; font-weight: 700; color: var(--red); line-height: 1; }
  .rules-list { list-style: none; left: 34px; top: 220px; }
  .rules-list li { display: flex; align-items: center; height: 40px; font-size: 12.5px; font-weight: 700; }
  .rules-list .icon { width: 28px; height: 28px; margin-right: 32px; stroke-width: 1.6; }
  .rules-list .no { color: var(--red); font-size: 17px; font-weight: 500; margin-right: 6px; }

  /* Sign 4 */
  .sign--climb { left: 709px; top: 715px; width: 401px; height: 160px; }
  .sign--climb .sign__panel { left: 14px; top: 13px; width: 373px; height: 134px; }
  .climb-icon { left: 20px; top: 36px; width: 66px; height: 62px; }
  .climb-title { left: 106px; top: 33px; font-size: 37px; font-weight: 700; line-height: 1; white-space: nowrap; }
  .climb-brand { left: 106px; width: 247px; top: 84px; }
  .climb-brand .brand__name { font-size: 14px; gap: 4px; }
  .climb-brand .brand__dot { width: 8px; height: 8px; }
  .climb-brand .brand__tag { font-size: 6px; margin-top: 1px; }
</style>
</head>
<body>

<section class="sign sign--age">
  <div class="sign__frame" role="img" aria-label="Rainbow striped border"></div>
  <div class="sign__panel">
    <div class="brand abs center" style="top:34px"><div class="brand__name">Pebble Hop<span class="brand__dot"></span></div><div class="brand__tag">MOBILE PLAY CENTRE</div></div>
    <h1 class="age-title abs center">0-3 YEAR OLDS ONLY</h1>
    <div class="age-note abs" style="top:196px">
      <svg class="icon" viewBox="0 0 36 36" aria-hidden="true"><path d="M3 18 Q18 6 33 18 Q18 30 3 18 Z"/><circle cx="18" cy="18" r="5" fill="var(--ink)"/></svg>
      <span><span class="accent">SUPERVISION</span> REQUIRED AT ALL TIMES</span>
    </div>
    <div class="age-note abs" style="top:245px">
      <svg class="icon" viewBox="0 0 36 36" aria-hidden="true"><path d="M10 3 H20 V20 L28 26 Q31 30 27 33 L12 27 Q8 25 10 20 Z" fill="var(--ink)"/></svg>
      <span>PARENTS PLEASE <span class="accent">WEAR SOCKS</span> TOO</span>
    </div>
  </div>
</section>

<section class="sign sign--toddler">
  <div class="sign__frame" role="img" aria-label="Rainbow striped border"></div>
  <div class="sign__panel">
    <div class="brand abs center" style="top:34px"><div class="brand__name">Pebble Hop<span class="brand__dot"></span></div><div class="brand__tag">MOBILE PLAY CENTRE</div></div>
    <p class="toddler-text abs center">
      <span class="accent">IF USING THE TODDLER SOFT PLAY EQUIPMENT,</span><br>
      PLEASE ENSURE THAT THIS AREA IS USED BY<br>
      CHILDREN&nbsp; <span class="accent big">0-3 ONLY.</span>&nbsp; THE EQUIPMENT AND BALL<br>
      PIT IS ONLY DESIGNED FOR SMALL CHILDREN AND<br>
      BIGGER KIDS MIGHT INJURE THEMSELVES, THE<br>
      SMALLER CHILDREN OR CAUSE EXTENSIVE<br>
      DAMAGE TO THE EQUIPMENT, OF WHICH THERE<br>
      WILL BE A CHARGE BACK TO THE CLIENT.
    </p>
  </div>
</section>

<section class="sign sign--rules">
  <div class="sign__frame" role="img" aria-label="Rainbow striped border"></div>
  <div class="sign__panel">
    <div class="brand abs center" style="top:30px"><div class="brand__name">Pebble Hop<span class="brand__dot"></span></div><div class="brand__tag">MOBILE PLAY CENTRE</div></div>
    <p class="rules-intro abs center">Parents/Guardians must supervise children<br>using this play equipment at all times</p>
    <h2 class="rules-title abs center">PLAY GROUND RULES</h2>
    <ul class="rules-list abs">
      <li><svg class="icon" viewBox="0 0 28 28" aria-hidden="true"><ellipse cx="9" cy="14" rx="5" ry="11"/><ellipse cx="19" cy="14" rx="5" ry="11"/></svg><span class="no">NO</span>SHOES – SOCKS MUST BE WORN</li>
      <li><svg class="icon" viewBox="0 0 28 28" aria-hidden="true"><rect x="3" y="3" width="22" height="22"/><path d="M3 10 H25 M3 17 H25 M10 3 V25 M17 3 V25 M3 3 L25 25 M25 3 L3 25"/></svg><span class="no">NO</span>CLIMBING THE NETS</li>
      <li><svg class="icon" viewBox="0 0 28 28" aria-hidden="true"><path d="M4 9 H14 L12.5 25 H5.5 Z M10 9 L12 2 H16"/><rect x="15" y="16" width="10" height="3"/><rect x="15" y="21" width="10" height="3"/></svg><span class="no">NO</span>FOOD OR DRINK</li>
      <li><svg class="icon" viewBox="0 0 28 28" aria-hidden="true"><path d="M8 2 H12 V6 L15 10 V26 H5 V10 L8 6 Z M5 16 H15"/><path d="M18 14 H25 L24 26 H19 Z"/></svg><span class="no">NO</span>BOTTLE OR GLASS</li>
      <li><svg class="icon" viewBox="0 0 28 28" aria-hidden="true"><circle cx="14" cy="9" r="6"/><circle cx="9" cy="18" r="6"/><circle cx="19" cy="19" r="6"/></svg><span class="no">NO</span>CHEWING GUM</li>
      <li><svg class="icon" viewBox="0 0 28 28" aria-hidden="true"><path d="M3 3 L25 25 M6 3 L10 10 M3 6 L10 10"/><path d="M25 3 L12 14 Q8 18 3 25"/></svg><span class="no">NO</span>SHARP OBJECTS</li>
      <li><svg class="icon" viewBox="0 0 28 28" aria-hidden="true"><path d="M24 3 L12 17"/><path d="M12 17 Q6 17 5 24 Q11 25 14 20 Z" fill="var(--ink)"/></svg><span class="no">NO</span>FACE PAINTING</li>
    </ul>
  </div>
</section>

<section class="sign sign--climb">
  <div class="sign__frame" role="img" aria-label="Rainbow striped border"></div>
  <div class="sign__panel">
    <svg class="climb-icon abs icon" viewBox="0 0 66 62" aria-hidden="true">
      <rect x="4" y="6" width="58" height="52" stroke-width="3"/>
      <path d="M4 20 H62 M4 34 H62 M4 48 H62 M18 6 V58 M33 6 V58 M48 6 V58 M4 6 L56 58 M20 6 L62 48 M4 22 L40 58 M62 6 L10 58 M46 6 L4 48 M62 22 L26 58"/>
      <line x1="0" y1="62" x2="66" y2="2" stroke="var(--red)" stroke-width="3.5"/>
    </svg>
    <div class="climb-title abs"><span class="accent">NO</span> CLIMBING</div>
    <div class="brand climb-brand abs"><div class="brand__name">Pebble Hop<span class="brand__dot"></span></div><div class="brand__tag">MOBILE PLAY CENTRE</div></div>
  </div>
</section>

</body>
</html>
```